Silver Bloom Marisol's Cleaning Service Business Cards Project

A business card with all contact details with logo design on there (already have a logo) eye catching Logo and contact info on one side, full logo on the back, must target upper class residential and corporate companies, fitness companies, still keep it on the feminine side of things , must look elegant

Target Market(s)

Upper class homes and corporate companies

Industry/Entity Type

Cleaning Service

Contact Information for Business Card

Name: Marisol Quenby
Position: Director
ABN: 31647209853
Email: marisolssilvercleaning@tidymail.example
Number: 0417906354

Font styles to use
Decorative

Colors

Designer to choose colors to be used in the design.

Requirements
Must have
• Available Sydney Wide, contact info and logo on one side, full logo on the back
Nice to have
• Professional appearance
Should not have
• Cheap advert looking stuff

```html
<!DOCTYPE html>
<html lang="en">
<head>
<meta charset="utf-8">
<title>Silver Bloom — Business Cards</title>
<link rel="stylesheet" href="https://fonts.googleapis.com/css2?family=Cinzel:wght@400&family=Oswald:wght@500&family=Open+Sans:wght@400&display=swap">
<style>
  :root {
    --page-bg: #e9e6e2;
    --card-bg: #2f3441;
    --silver: #b9bcc2;
    --silver-soft: #a7abb3;
    --line: #8c9099;
  }
  * { margin: 0; padding: 0; box-sizing: border-box; }
  html, body { width: 1200px; height: 1000px; overflow: hidden; }
  body {
    background: var(--page-bg);
    position: relative;
    font-family: "Open Sans", Arial, sans-serif;
  }
  .card {
    position: absolute;
    left: 266px;
    width: 666px;
    background: var(--card-bg);
    border-radius: 24px;
  }
  .card--front { top: 75px; height: 395px; }
  .card--back { top: 533px; height: 397px; }

  .brand-mark {
    position: absolute;
    left: 50%;
    top: 92px;
    width: 92px;
    height: 92px;
    margin-left: -46px;
    border: 2px solid var(--silver);
    border-radius: 50%;
  }
  .brand-name, .brand-tagline {
    position: absolute;
    left: 0;
    width: 100%;
    text-align: center;
    font-family: "Cinzel", Georgia, serif;
    font-weight: 400;
    color: var(--silver);
  }
  .brand-name { top: 262px; font-size: 37px; letter-spacing: 1px; }
  .brand-tagline { top: 312px; font-size: 13px; letter-spacing: 3.4px; }

  .holder {
    position: absolute;
    right: 415px;
    top: 168px;
    text-align: right;
  }
  .holder-name {
    font-family: "Oswald", "Arial Narrow", sans-serif;
    font-weight: 500;
    font-size: 22px;
    color: var(--silver);
    letter-spacing: 0.3px;
    line-height: 30px;
    text-transform: uppercase;
  }
  .holder-role {
    font-size: 15px;
    color: var(--silver-soft);
    line-height: 20px;
  }
  .divider {
    position: absolute;
    left: 270px;
    top: 168px;
    width: 1px;
    height: 56px;
    background: var(--line);
  }
  .contact-list {
    position: absolute;
    left: 286px;
    top: 164px;
    list-style: none;
    font-size: 15px;
    line-height: 22px;
    color: var(--silver);
  }
  .contact-list li { display: flex; align-items: center; gap: 6px; white-space: nowrap; }
  .contact-list svg { width: 13px; height: 13px; flex: none; }
</style>
</head>
<body>
  <section class="card card--front" aria-label="Card front">
    <div class="brand-mark"></div>
    <h1 class="brand-name">SILVER BLOOM</h1>
    <p class="brand-tagline">MARISOL'S CLEANING SERVICE</p>
  </section>

  <section class="card card--back" aria-label="Card back">
    <div class="holder">
      <p class="holder-name">Marisol Quenby</p>
      <p class="holder-role">Director</p>
    </div>
    <div class="divider"></div>
    <ul class="contact-list">
      <li>ABN: 31647209853</li>
      <li>
        <svg viewBox="0 0 16 16" aria-hidden="true"><path d="M3.5 1.5l2.5 0 1 3.5-1.8 1.2c.8 1.8 2.3 3.3 4.1 4.1L10.5 8.5 14 9.5v2.5c0 1-1 2-2 2C6.5 14 2 9.5 1.5 4c0-1.3 1-2.5 2-2.5z" fill="none" stroke="currentColor" stroke-width="1.3" stroke-linejoin="round"/></svg>
        0417906354
      </li>
      <li>
        <svg viewBox="0 0 16 16" aria-hidden="true"><rect x="1.5" y="3.5" width="13" height="9" fill="none" stroke="currentColor" stroke-width="1.3"/><path d="M1.5 3.5l6.5 5 6.5-5" fill="none" stroke="currentColor" stroke-width="1.3"/></svg>
        marisolssilvercleaning@tidymail.example
      </li>
    </ul>
  </section>
</body>
</html>
```